FernPath....... a dash of Glow

I need a web design for a new business based in London that will be mobile (offered at homes, parks or a local cafe ect) called FernPath. I offer Life Coaching/Counselling sessions, Personal training, Massage and Sports Massage. Sessions range from an hour to half and hour. My aim is to help people along their journey to help give them gain clarity of where there going, helping them to towards their goals, so that can experience bliss. My website should represent a place people can come to release their stress and worries so that they leave feeling lighter, clearer and happier. I would like my website to reflect someone feeling ALIVE. I would also like a logo design for FernPath with a sentence underneath or near saying a touch of bliss.

Target Market(s)

middle class people

Industry/Entity Type

Business

Coding

Coded - Design and coding required

Number of Pages Required

4 page

Requirements
Must have
• 1st page About us
• 2nd page Services
• 3rd page Prices
• 4th page contact details
Nice to have
• mixture of cultures in images

```html
<!DOCTYPE html>
<html lang="en">
<head>
<meta charset="utf-8">
<title>FernPath — a dash of Glow</title>
<link rel="stylesheet" href="https://fonts.googleapis.com/css2?family=Raleway:wght@400;600;700;800&family=Open+Sans:ital,wght@0,400;0,600;0,700;1,400&display=swap">
<style>
:root{
  --teal:#2a9d86;
  --teal-dark:#238a75;
  --mint:#3ecfa9;
  --ink:#333a3f;
  --muted:#5b6166;
  --grey-title:#d4d6d8;
  --rule:#3ecfa9;
  --dark:#2a2a2a;
  --white:#ffffff;
  --footer:#ffffff;
}
*{box-sizing:border-box;margin:0;padding:0}
html,body{width:1200px;height:3429px;overflow:hidden;background:var(--white)}
body{font-family:"Open Sans",Arial,sans-serif;color:var(--ink);font-size:13px}
.page{width:1200px;height:3429px;position:relative}

/* header */
.site-header{height:80px;display:flex;align-items:center;padding:0 100px;justify-content:space-between}
.brand{display:flex;align-items:center;gap:14px}
.brand-dot{width:48px;height:48px;border-radius:50%;background:var(--teal)}
.brand-name{font-family:"Raleway",sans-serif;font-weight:700;color:var(--teal);font-size:22px;line-height:1.05;letter-spacing:.5px}
.brand-name small{display:block;font-size:15px;font-weight:700;letter-spacing:1px}
.main-nav{display:flex;align-items:center;gap:52px}
.main-nav a{font-family:"Raleway",sans-serif;font-size:12px;font-weight:600;color:var(--ink);text-decoration:none;letter-spacing:.5px}
.search-btn{width:36px;height:36px;border-radius:50%;background:var(--teal);display:flex;align-items:center;justify-content:center;margin-left:-10px}

/* hero */
.hero{position:relative;height:518px}
.hero-photo{position:absolute;inset:0;background:linear-gradient(180deg,#e9f1c6 0%,#f2f3bf 35%,#8fb7b5 62%,#3f6d79 78%,#6b4b2e 100%)}
.hero-copy{position:absolute;left:683px;top:150px;width:430px}
.hero-title{font-family:"Raleway",sans-serif;font-weight:700;font-size:42px;color:var(--teal);letter-spacing:.5px}
.hero-text{font-size:13px;line-height:29px;color:var(--ink);margin-top:10px}
.btn{display:inline-block;background:var(--mint);color:var(--white);font-family:"Raleway",sans-serif;font-weight:700;font-size:12px;letter-spacing:.5px;border-radius:22px;text-decoration:none;text-align:center}
.hero .btn{width:164px;height:44px;line-height:44px;margin-top:18px}
.hero-dots{position:absolute;left:578px;bottom:20px;display:flex;gap:8px}
.hero-dots span{width:8px;height:8px;border-radius:50%;background:rgba(255,255,255,.55)}
.hero-dots span:first-child{background:#fff}

/* sections */
.section-head{text-align:center}
.section-title{font-family:"Raleway",sans-serif;font-weight:700;font-size:22px;letter-spacing:.5px;color:var(--ink)}
.section-rule{width:52px;height:3px;background:var(--rule);margin:12px auto 0}
.section-lead{width:820px;margin:34px auto 0;text-align:center;font-size:11.5px;line-height:26px;color:var(--muted)}

.welcome{height:385px;text-align:center;padding-top:65px}
.welcome-title{font-family:"Raleway",sans-serif;font-weight:800;font-size:50px;color:var(--grey-title);letter-spacing:1px}
.welcome-text{width:840px;margin:22px auto 0;font-size:13px;line-height:31px;color:var(--muted)}
.welcome .btn,.services .btn{width:164px;height:44px;line-height:44px;margin-top:30px}

.services{height:813px;padding-top:0}
.service-grid{width:1000px;margin:44px auto 0;display:grid;grid-template-columns:repeat(4,1fr);gap:8px 8px}
.service-card{height:240px}
.service-photo{height:180px}
.service-label{height:60px;background:var(--teal);color:#fff;text-align:center;padding-top:13px}
.service-label h3{font-family:"Raleway",sans-serif;font-size:12px;font-weight:700;letter-spacing:.3px}
.service-label p{font-size:9.5px;font-style:italic;margin-top:4px}
.services .center{text-align:center}

.about{position:relative;height:432px;color:#fff;text-align:center}
.about-photo{position:absolute;inset:0;background:linear-gradient(90deg,#2b2b2b 0%,#3d3d3d 45%,#6a6a6a 72%,#3a3a3a 100%)}
.about-body{position:relative;padding-top:90px}
.about .section-title{color:#fff}
.about-text{width:820px;margin:20px auto 0;font-size:11.5px;line-height:26px}
.about .btn{width:164px;height:44px;line-height:44px;margin-top:28px}

.what{height:530px;padding-top:72px}
.features{width:880px;margin:52px auto 0;display:grid;grid-template-columns:1fr 1fr;gap:44px 80px;padding-left:30px}
.feature{display:flex;gap:24px}
.feature-icon{width:40px;flex:none}
.feature h4{font-family:"Open Sans",sans-serif;font-size:13px;font-weight:700;color:var(--ink)}
.feature p{font-size:11.5px;line-height:25px;color:var(--muted);margin-top:6px}

.testimonials{height:502px;background:var(--teal);color:#fff;text-align:center;padding-top:62px;position:relative}
.testimonials .section-title{color:#fff}
.quote{width:800px;margin:22px auto 0;font-style:italic;font-size:11.5px;line-height:27px;position:relative}
.quote-mark{position:absolute;font-family:"Raleway",sans-serif;font-size:44px;color:rgba(255,255,255,.45);font-style:normal}
.q-open{left:-24px;top:-10px}.q-close{right:-40px;bottom:-44px}
.t-dots{display:flex;justify-content:center;gap:8px;margin-top:22px}
.t-dots span{width:6px;height:6px;border-radius:50%;background:rgba(255,255,255,.5)}
.t-dots span:first-child{background:#fff}
.avatar{width:142px;height:142px;border-radius:50%;margin:22px auto 0;border:3px solid #fff;background:radial-gradient(circle at 50% 40%,#d9a58a 0%,#9c6a4f 55%,#5c3d2e 100%)}
.client{margin-top:14px;font-weight:700;font-size:13px}
.client em{font-weight:400;font-size:10px;margin-left:4px}

.site-footer{height:189px;text-align:center;padding-top:42px}
.footer-nav{display:flex;justify-content:center;gap:40px}
.footer-nav a{font-size:10.5px;color:var(--ink);text-decoration:none;letter-spacing:.3px}
.footer-legal{display:flex;justify-content:center;gap:26px;margin-top:22px;font-size:10.5px;color:var(--ink)}
.social{display:flex;justify-content:center;gap:12px;margin-top:26px}
.social span{width:32px;height:32px;border-radius:50%;background:var(--teal)}
</style>
</head>
<body>
<div class="page">

<header class="site-header">
  <div class="brand">
    <span class="brand-dot"></span>
    <div class="brand-name">FERNPATH<small>A DASH OF GLOW</small></div>
  </div>
  <nav class="main-nav">
    <a href="#">ABOUT US</a>
    <a href="#">SERVICES</a>
    <a href="#">WHAT WE DO?</a>
    <a href="#">TESTIMONIALS</a>
    <a href="#">CONTACT US</a>
    <span class="search-btn"><svg width="16" height="16" viewBox="0 0 16 16"><circle cx="6.5" cy="6.5" r="4.5" fill="none" stroke="#fff" stroke-width="2"/><line x1="10" y1="10" x2="14" y2="14" stroke="#fff" stroke-width="2.2" stroke-linecap="round"/></svg></span>
  </nav>
</header>

<section class="hero">
  <div class="hero-photo" role="img" aria-label="Woman in a yoga lunge on rocks by the sea at sunrise"></div>
  <div class="hero-copy">
    <h1 class="hero-title">A DASH OF GLOW</h1>
    <p class="hero-text">I offer Life Coaching/Counselling sessions, Personal training, Massage and Sports Massage. Sessions range from an hour to half and hour.</p>
    <a class="btn" href="#">SUBSCRIBE</a>
  </div>
  <div class="hero-dots"><span></span><span></span></div>
</section>

<section class="welcome">
  <h2 class="welcome-title">WELCOME TO FERNPATH</h2>
  <p class="welcome-text">Lorem Ipsum is simply dummy text of the printing and typesetting industry. Lorem Ipsum has been the industry's standard dummy text ever since the 1500s, when an unknown printer took a galley of type and scrambled it to make a type specimen book. It has survived not only five centuries, but also the leap into electronic typesetting</p>
  <a class="btn" href="#">VIEW HISTORY</a>
</section>

<section class="services">
  <div class="section-head">
    <h2 class="section-title">OUR SERVICES</h2>
    <div class="section-rule"></div>
    <p class="section-lead">Lorem Ipsum is simply dummy text of the printing and typesetting industry. Lorem Ipsum has been the industry's standard dummy text ever since the 1500s, when an unknown printer took a galley of type and scrambled it to make a type specimen book.</p>
  </div>
  <div class="service-grid">
    <div class="service-card"><div class="service-photo" role="img" aria-label="Couple cycling together outdoors" style="background:linear-gradient(160deg,#cfe0a8,#6f9a4a)"></div><div class="service-label"><h3>COACHING</h3><p>Click here for view details</p></div></div>
    <div class="service-card"><div class="service-photo" role="img" aria-label="Counsellor listening to a client" style="background:linear-gradient(160deg,#e6ebef,#8aa3b5)"></div><div class="service-label"><h3>COUNSELLING SESSIONS</h3><p>Click here for view details</p></div></div>
    <div class="service-card"><div class="service-photo" role="img" aria-label="Woman resting her chin on her hand" style="background:linear-gradient(160deg,#d8c2ad,#8a6a55)"></div><div class="service-label"><h3>PERSONAL TRAINING</h3><p>Click here for view details</p></div></div>
    <div class="service-card"><div class="service-photo" role="img" aria-label="Woman receiving a relaxing massage" style="background:linear-gradient(160deg,#7fa6a8,#c89a7c)"></div><div class="service-label"><h3>MASSAGE</h3><p>Click here for view details</p></div></div>
    <div class="service-card"><div class="service-photo" role="img" aria-label="Two women stretching on a studio floor" style="background:linear-gradient(160deg,#f0b56a,#c8552c)"></div><div class="service-label"><h3>SPORTS MASSAGE</h3><p>Click here for view details</p></div></div>
    <div class="service-card"><div class="service-photo" role="img" aria-label="Smiling older couple by the sea" style="background:linear-gradient(160deg,#c9dbe8,#8fa7b7)"></div><div class="service-label"><h3>LOREM IPSUM IS SIMPLY</h3><p>Click here for view details</p></div></div>
    <div class="service-card"><div class="service-photo" role="img" aria-label="Woman raising her arms in the sunshine" style="background:linear-gradient(160deg,#f4e6c4,#c7a77e)"></div><div class="service-label"><h3>LOREM IPSUM IS SIMPLY</h3><p>Click here for view details</p></div></div>
    <div class="service-card"><div class="service-photo" role="img" aria-label="Woman meditating on grass in a park" style="background:linear-gradient(160deg,#c7dd8e,#4f8a3a)"></div><div class="service-label"><h3>LOREM IPSUM IS SIMPLY</h3><p>Click here for view details</p></div></div>
  </div>
  <div class="center"><a class="btn" href="#">VIEW MORE</a></div>
</section>

<section class="about">
  <div class="about-photo" role="img" aria-label="Dark monochrome portrait of a woman relaxing"></div>
  <div class="about-body">
    <h2 class="section-title">ABOUT FERNPATH</h2>
    <p class="about-text">Lorem Ipsum is simply dummy text of the printing and typesetting industry. Lorem Ipsum has been the industry's standard dummy text ever since the 1500s, when an unknown printer took a galley of type and scrambled it to make a type specimen book Lorem Ipsum is simply dummy text of the printing and typesetting industry. Lorem Ipsum has been the industry's standard dummy text ever since the 1500s, when an unknown printer took a galley of type and scrambled it to make a type specimen book.</p>
    <a class="btn" href="#">READ MORE</a>
  </div>
</section>

<section class="what">
  <div class="section-head">
    <h2 class="section-title">WHAT WE DO?</h2>
    <div class="section-rule"></div>
    <p class="section-lead">Lorem Ipsum is simply dummy text of the printing and typesetting industry. Lorem Ipsum has been the industry's standard dummy text ever since the 1500s, when an unknown printer took a galley of type and scrambled it to make a type specimen book.</p>
  </div>
  <div class="features">
    <div class="feature">
      <svg class="feature-icon" viewBox="0 0 40 40" height="40"><path d="M20 36 V16" stroke="#2a9d86" stroke-width="3" fill="none"/><path d="M20 20 C10 20 6 12 8 6 C16 6 20 12 20 20Z" fill="#2a9d86"/><path d="M20 26 C30 26 34 18 32 12 C24 12 20 18 20 26Z" fill="#2a9d86"/></svg>
      <div><h4>Lorem Ipsum is simply dummy</h4><p>Lorem Ipsum is simply dummy text of the printing and typesetting industry. Lorem Ipsum has been the industry...</p></div>
    </div>
    <div class="feature">
      <svg class="feature-icon" viewBox="0 0 40 40" height="40"><path d="M20 4 C24 12 30 16 30 25 A10 10 0 0 1 10 25 C10 18 16 15 16 9 C19 12 20 14 20 4Z" fill="#2a9d86"/></svg>
      <div><h4>Lorem Ipsum is simply dummy</h4><p>Lorem Ipsum is simply dummy text of the printing and typesetting industry. Lorem Ipsum has been the industry...</p></div>
    </div>
    <div class="feature">
      <svg class="feature-icon" viewBox="0 0 40 40" height="40"><ellipse cx="17" cy="16" rx="14" ry="10" fill="none" stroke="#2a9d86" stroke-width="3"/><path d="M8 24 L5 33 L15 26" fill="#2a9d86"/><path d="M26 27 C32 27 37 24 37 19" stroke="#2a9d86" stroke-width="3" fill="none"/></svg>
      <div><h4>Lorem Ipsum is simply dummy</h4><p>Lorem Ipsum is simply dummy text of the printing and typesetting industry. Lorem Ipsum has been the industry...</p></div>
    </div>
    <div class="feature">
      <svg class="feature-icon" viewBox="0 0 40 40" height="40"><circle cx="11" cy="11" r="5" fill="#2a9d86"/><circle cx="29" cy="11" r="5" fill="#2a9d86"/><circle cx="20" cy="19" r="6" fill="#2a9d86"/><rect x="4" y="18" width="12" height="10" rx="4" fill="#2a9d86"/><rect x="24" y="18" width="12" height="10" rx="4" fill="#2a9d86"/><rect x="12" y="26" width="16" height="11" rx="4" fill="#2a9d86"/></svg>
      <div><h4>Lorem Ipsum is simply dummy</h4><p>Lorem Ipsum is simply dummy text of the printing and typesetting industry. Lorem Ipsum has been the industry...</p></div>
    </div>
  </div>
</section>

<section class="testimonials">
  <h2 class="section-title">WHAT OUR CLIENT'S SAY</h2>
  <blockquote class="quote">
    <span class="quote-mark q-open">“</span>
    Lorem Ipsum is simply dummy text of the printing and typesetting industry. Lorem Ipsum has been the industry's standard dummy text ever since the 1500s, when an unknown printer took a galley of type and scrambled it to make a type specimen book. It has survived not only five centuries, but also the leap into electronic typesetting, remaining
    <span class="quote-mark q-close">”</span>
  </blockquote>
  <div class="t-dots"><span></span><span></span><span></span></div>
  <div class="avatar" role="img" aria-label="Portrait photo of the client"></div>
  <p class="client">Lena Marsh<em>House wife</em></p>
</section>

<footer class="site-footer">
  <nav class="footer-nav">
    <a href="#">HOME</a><a href="#">ABOUT US</a><a href="#">SERVICES</a><a href="#">WHAT WE DO?</a><a href="#">TESTIMONIALS</a><a href="#">CONTACT US</a>
  </nav>
  <div class="footer-legal"><span>© 2015. FERNPATH. ALL RIGHTS RESERVED</span><span>TERMS OF USE</span><span>PRIVACY POLICY</span></div>
  <div class="social" aria-label="Social links"><span></span><span></span><span></span><span></span><span></span></div>
</footer>

</div>
</body>
</html>
```